New Webpage for High Class Expert Witness Services Company

We are looking for a minimalist design for a webpage that just has our logo and an entry form offer to connect with one of our Liaisons.
The entry form should just ask for Name, Email, Contact Info and Description of Project.

Company Name is: The Marlowe Crest Advisory Services

Number of Pages Required

1 page

```html
<!DOCTYPE html>
<html lang="en">
<head>
<meta charset="utf-8">
<title>The Marlowe Crest Advisory Services — Witness Services</title>
<link rel="stylesheet" href="https://fonts.googleapis.com/css2?family=Gilda+Display&family=Outfit:wght@400;500&display=swap">
<style>
  :root {
    --night: #07070c;
    --night-mid: #1b1a22;
    --night-warm: #2a2418;
    --ink: #000000;
    --paper: #ffffff;
    --line: #3a3a3a;
    --band-light: #e8e8ea;
    --band-dark: #8f9096;
    --footer-text: #1a1a1a;
  }
  * { box-sizing: border-box; margin: 0; padding: 0; }
  html, body { width: 1200px; height: 708px; overflow: hidden; background: var(--paper); }
  body { position: relative; font-family: "Outfit", sans-serif; }

  .hero { position: absolute; left: 0; top: 0; width: 1200px; height: 662px; overflow: hidden; }
  .hero-photo {
    position: absolute; inset: 0;
    background:
      radial-gradient(ellipse 70% 35% at 40% 62%, rgba(120,100,60,0.35), transparent 70%),
      linear-gradient(180deg, var(--night) 0%, var(--night-mid) 45%, var(--night-warm) 62%, var(--night) 100%);
  }
  .hero-band { position: absolute; inset: 0; }

  .brand {
    position: absolute; top: 50px; left: 0; width: 1200px;
    display: flex; justify-content: center; align-items: center; gap: 12px;
    font-family: "Gilda Display", serif; font-size: 28px; color: #d8d8da; letter-spacing: 1px;
  }
  .brand-mark { width: 22px; height: 22px; background: #d8d8da; }

  .intro { position: absolute; left: 62px; top: 0; width: 600px; height: 662px; color: var(--paper); }
  .intro > * { position: absolute; left: 0; white-space: nowrap; }
  .eyebrow {
    top: 140px;
    font-family: "Gilda Display", serif; font-size: 50px; line-height: 56px;
    color: transparent; -webkit-text-stroke: 1px rgba(255,255,255,0.75);
  }
  .headline {
    top: 202px;
    font-family: "Gilda Display", serif; font-weight: 400; font-size: 74px; line-height: 89px;
  }
  .lede { top: 478px; width: 530px; white-space: normal; font-size: 14px; line-height: 19px; }
  .assurances { top: 538px; font-family: "Gilda Display", serif; font-size: 25px; line-height: 32px; }

  .contact-card {
    position: absolute; left: 612px; top: 146px; width: 525px; height: 417px;
    background: var(--paper); border-radius: 13px; padding: 33px 33px 0;
  }
  .field { display: block; border-bottom: 1px solid var(--line); }
  .field span { display: block; font-size: 13px; color: var(--ink); }
  .field input, .field textarea {
    display: block; width: 100%; border: 0; outline: 0; background: transparent;
    font-family: inherit; font-size: 13px; resize: none;
  }
  .fields .field:nth-child(1) { height: 38px; }
  .fields .field:nth-child(2), .fields .field:nth-child(3) { height: 71px; padding-top: 33px; }
  .fields .field:nth-child(4) { height: 94px; padding-top: 33px; }
  .submit {
    margin-top: 33px; width: 142px; height: 45px; border: 0; background: var(--ink); color: var(--paper);
    font-family: "Outfit", sans-serif; font-weight: 500; font-size: 15px;
  }

  .site-footer {
    position: absolute; left: 0; top: 662px; width: 1200px; height: 46px;
    display: flex; align-items: center; justify-content: center;
    font-size: 12px; color: var(--footer-text);
  }
</style>
</head>
<body>
  <section class="hero">
    <div class="hero-photo" role="img" aria-label="Night skyline of a waterfront city with a lit bridge reflected in the bay"></div>
    <svg class="hero-band" width="1200" height="662" viewBox="0 0 1200 662" aria-hidden="true">
      <defs>
        <linearGradient id="bandShade" x1="0" y1="0" x2="0" y2="1">
          <stop offset="0" stop-color="#e8e8ea"/>
          <stop offset="1" stop-color="#8f9096"/>
        </linearGradient>
      </defs>
      <path d="M1152 0 L1200 0 L1200 170 Q1030 420 900 662 L768 662 Q880 420 1020 148 Q1080 70 1152 0 Z" fill="url(#bandShade)"/>
    </svg>

    <div class="brand"><span class="brand-mark"></span>The Marlowe Crest Advisory Services</div>

    <div class="intro">
      <p class="eyebrow">WITNESS SERVICES</p>
      <h1 class="headline">Need an Expert<br>—Witness for<br>Your Case?</h1>
      <p class="lede">We connect law firms and insurers with verified expert witnesses across medical and technical fields.</p>
      <p class="assurances">Confidential · Fast Response · Verified Experts</p>
    </div>

    <form class="contact-card">
      <div class="fields">
        <label class="field"><span>Full Name*</span><input type="text" name="name"></label>
        <label class="field"><span>Email Address*</span><input type="email" name="email"></label>
        <label class="field"><span>Phone Number*</span><input type="tel" name="phone"></label>
        <label class="field"><span>Your message......</span><textarea name="message" rows="2"></textarea></label>
      </div>
      <button class="submit" type="button">Submit</button>
    </form>
  </section>

  <footer class="site-footer">Copyright © 2026 The Marlowe Crest Advisory Services. All Rights Reserved.</footer>
</body>
</html>
```